hotel amenities supply company needs design for bottles and accessories

we need to design four 30ml amenity tubes branded "ORVELLE" , shampoo, shower gel, conditioner and body lotion. the bottle has to be somewhat clear to be able to see the liquid inside. its basically designing the complete identity for "orvelle". attached are some examples. also the accessory boxes should match the design eg, shaving kit,vanity kit, toothbrush etc

Target Market(s)

hotels

Industry/Entity Type

Hotel

Font styles to use
Script

Requirements
Must have
• name "orvelle " on bottles and product info
Should not have
• dark colors

```html
<!DOCTYPE html>
<html lang="en">
<head>
<meta charset="utf-8">
<title>Orvelle Amenity Tubes</title>
<link rel="stylesheet" href="https://fonts.googleapis.com/css2?family=Great+Vibes&family=Raleway:wght@400&display=swap">
<style>
  :root {
    --bg-top: #565656;
    --bg-bottom: #c2c2c2;
    --crimp: #e2e2e2;
    --cap: #f7f7f7;
    --cap-edge: #dcdcdc;
    --clear-top: rgba(244, 244, 244, 0.95);

    --shampoo-ink: #e8202a;
    --shampoo-soft: #ff5f6e;
    --shampoo-liquid: #d9d7ba;

    --conditioner-ink: #d81fb4;
    --conditioner-soft: #ff66dc;
    --conditioner-liquid: #dadada;

    --showergel-ink: #1c7a2a;
    --showergel-soft: #3ea85c;
    --showergel-liquid: #d8d7af;

    --lotion-ink: #1d68d8;
    --lotion-soft: #5aa9ff;
    --lotion-liquid: #c2eef0;

    --script: "Great Vibes", cursive;
    --sans: "Raleway", sans-serif;
  }

  * { box-sizing: border-box; margin: 0; padding: 0; }

  html, body {
    width: 1200px;
    height: 640px;
    overflow: hidden;
  }

  .range {
    position: relative;
    width: 1200px;
    height: 640px;
    background: linear-gradient(to bottom, var(--bg-top), var(--bg-bottom));
  }

  .tube {
    position: absolute;
    top: 88px;
    width: 218px;
    height: 510px;
  }
  .tube--shampoo     { left: 114px; --ink: var(--shampoo-ink);     --soft: var(--shampoo-soft);     --liquid: var(--shampoo-liquid); }
  .tube--conditioner { left: 367px; --ink: var(--conditioner-ink); --soft: var(--conditioner-soft); --liquid: var(--conditioner-liquid); }
  .tube--showergel   { left: 619px; --ink: var(--showergel-ink);   --soft: var(--showergel-soft);   --liquid: var(--showergel-liquid); }
  .tube--lotion      { left: 873px; --ink: var(--lotion-ink);      --soft: var(--lotion-soft);      --liquid: var(--lotion-liquid); }

  .tube__crimp {
    position: absolute;
    top: 0;
    left: 0;
    width: 218px;
    height: 22px;
    background: var(--crimp);
    border-radius: 3px 3px 0 0;
  }

  .tube__body {
    position: absolute;
    top: 20px;
    left: 0;
    width: 218px;
    height: 426px;
    clip-path: polygon(0 0, 100% 0, 78.5% 100%, 21.5% 100%);
    background: linear-gradient(to bottom, var(--clear-top) 0%, var(--clear-top) 10%, var(--liquid) 32%, var(--liquid) 100%);
  }

  .tube__wreath {
    position: absolute;
    top: 10px;
    left: 0;
    width: 218px;
    height: 260px;
  }

  .tube__mark {
    position: absolute;
    top: 22px;
    left: 50%;
    width: 26px;
    height: 26px;
    margin-left: -13px;
    border-radius: 50%;
    background: var(--soft);
  }

  .tube__brand {
    position: absolute;
    top: 56px;
    left: 0;
    width: 100%;
    text-align: center;
    font-family: var(--script);
    font-size: 54px;
    line-height: 1;
    color: var(--soft);
  }

  .tube__product {
    position: absolute;
    bottom: 20px;
    left: 50%;
    transform: translateX(-50%) rotate(180deg);
    writing-mode: vertical-rl;
    font-family: var(--sans);
    font-weight: 400;
    font-size: 28px;
    letter-spacing: 0.5px;
    text-transform: uppercase;
    color: var(--ink);
    line-height: 1;
    white-space: nowrap;
  }

  .tube__band {
    position: absolute;
    bottom: 0;
    left: 0;
    width: 100%;
    height: 9px;
    background: var(--ink);
  }

  .tube__cap {
    position: absolute;
    top: 446px;
    left: 47px;
    width: 124px;
    height: 58px;
    background: linear-gradient(to right, var(--cap-edge), var(--cap) 30%, var(--cap) 70%, var(--cap-edge));
    border-radius: 0 0 4px 4px;
  }
</style>
</head>
<body>
  <main class="range">

    <article class="tube tube--shampoo">
      <div class="tube__crimp"></div>
      <div class="tube__body">
        <svg class="tube__wreath" viewBox="0 0 218 260" role="img" aria-label="Leaf wreath ornament framing the name">
          <path d="M28 250 C 14 130, 44 30, 109 18 C 174 30, 204 130, 190 250" fill="none" stroke="var(--ink)" stroke-width="26" stroke-opacity="0.22"/>
        </svg>
        <span class="tube__mark"></span>
        <p class="tube__brand">Orvelle</p>
        <p class="tube__product">Shampoo</p>
        <span class="tube__band"></span>
      </div>
      <div class="tube__cap"></div>
    </article>

    <article class="tube tube--conditioner">
      <div class="tube__crimp"></div>
      <div class="tube__body">
        <svg class="tube__wreath" viewBox="0 0 218 260" role="img" aria-label="Leaf wreath ornament framing the name">
          <path d="M28 250 C 14 130, 44 30, 109 18 C 174 30, 204 130, 190 250" fill="none" stroke="var(--ink)" stroke-width="26" stroke-opacity="0.22"/>
        </svg>
        <span class="tube__mark"></span>
        <p class="tube__brand">Orvelle</p>
        <p class="tube__product">Conditioner</p>
        <span class="tube__band"></span>
      </div>
      <div class="tube__cap"></div>
    </article>

    <article class="tube tube--showergel">
      <div class="tube__crimp"></div>
      <div class="tube__body">
        <svg class="tube__wreath" viewBox="0 0 218 260" role="img" aria-label="Leaf wreath ornament framing the name">
          <path d="M28 250 C 14 130, 44 30, 109 18 C 174 30, 204 130, 190 250" fill="none" stroke="var(--ink)" stroke-width="26" stroke-opacity="0.22"/>
        </svg>
        <span class="tube__mark"></span>
        <p class="tube__brand">Orvelle</p>
        <p class="tube__product">Shower Gel</p>
        <span class="tube__band"></span>
      </div>
      <div class="tube__cap"></div>
    </article>

    <article class="tube tube--lotion">
      <div class="tube__crimp"></div>
      <div class="tube__body">
        <svg class="tube__wreath" viewBox="0 0 218 260" role="img" aria-label="Leaf wreath ornament framing the name">
          <path d="M28 250 C 14 130, 44 30, 109 18 C 174 30, 204 130, 190 250" fill="none" stroke="var(--ink)" stroke-width="26" stroke-opacity="0.22"/>
        </svg>
        <span class="tube__mark"></span>
        <p class="tube__brand">Orvelle</p>
        <p class="tube__product">Body Lotion</p>
        <span class="tube__band"></span>
      </div>
      <div class="tube__cap"></div>
    </article>

  </main>
</body>
</html>
```